1876 Basins & Spouts Business Card

I'm wanting to get a business card designed. Our business is 1876 Basins & Spouts
Details for the card:

1876 Basins & Spouts
Name: Harold Vesk
Email: harold@1876basinsandspouts.com.au
Website: www.1876basinsandspouts.com.au
Mobile: 0438 260 947
Phone: 02 7481 3926

Font of Basins & Spouts is called Snell Roundhand. Not sue what font logo text is.

I'm thinking two sided but it doesn't have to be.

```html
<!DOCTYPE html>
<html lang="en">
<head>
<meta charset="utf-8">
<title>1876 Basins &amp; Spouts — Business Card</title>
<link rel="stylesheet" href="https://fonts.googleapis.com/css2?family=Pinyon+Script&family=Open+Sans:wght@400;700&display=swap">
<style>
  :root {
    --bg: #2a2a2b;
    --card: #1e1f21;
    --card-back: #1b1c1e;
    --pattern: #232427;
    --ink: #f2f2f2;
    --ink-soft: #b9babc;
    --rule: #6d6e70;
  }
  * { margin: 0; padding: 0; box-sizing: border-box; }
  html, body {
    width: 1200px; height: 1108px; overflow: hidden;
    background: var(--bg);
  }
  .stage {
    position: relative; width: 1200px; height: 1108px;
    display: flex; justify-content: center; align-items: center; gap: 60px;
  }
  .card {
    position: relative; width: 460px; height: 720px;
    border-radius: 30px; overflow: hidden;
    box-shadow: 0 14px 40px rgba(0,0,0,.45);
  }
  .card--front { background: var(--card); }
  .card--back { background: var(--card-back); }

  .brand {
    position: absolute; left: 42px; right: 30px; top: 150px;
  }
  .brand__name {
    font-family: "Open Sans", sans-serif; font-weight: 400;
    font-size: 28px; color: var(--ink); line-height: 1.1;
    white-space: nowrap;
  }
  .brand__tagline {
    margin-top: 10px;
    font-family: "Open Sans", sans-serif; font-size: 11px;
    color: var(--ink-soft); letter-spacing: .2px; white-space: nowrap;
  }

  .person {
    position: absolute; left: 0; right: 0; top: 440px;
    text-align: center;
  }
  .person__name {
    font-family: "Pinyon Script", cursive; font-weight: 400;
    font-size: 44px; color: var(--ink); line-height: 1.1;
  }
  .person__rule {
    width: 170px; height: 1px; background: var(--rule);
    margin: 14px auto 16px;
  }
  .contact {
    font-family: "Open Sans", sans-serif; font-size: 19px;
    color: var(--ink-soft); line-height: 1.28; list-style: none;
  }
  .contact b { color: var(--ink); }

  .pattern-field {
    position: absolute; inset: 0;
    background: radial-gradient(circle at 50% 40%, var(--pattern), var(--card-back) 75%);
  }
  .back-name {
    position: absolute; left: 0; right: 0; top: 560px;
    text-align: center;
    font-family: "Open Sans", sans-serif; font-size: 16px;
    color: var(--ink-soft);
  }
</style>
</head>
<body>
  <main class="stage">
    <section class="card card--front" aria-label="Card front">
      <div class="brand">
        <p class="brand__name">1876 Basins &amp; Spouts</p>
        <p class="brand__tagline">Quality fixtures for classic kitchens and bathrooms</p>
      </div>

      <div class="person">
        <h1 class="person__name">Harold Vesk</h1>
        <div class="person__rule"></div>
        <ul class="contact">
          <li><b>P:</b> 0438 260 947</li>
          <li><b>M:</b> 02 7481 3926</li>
          <li>harold@1876basinsandspouts.com.au</li>
          <li>www.1876basinsandspouts.com.au</li>
        </ul>
      </div>
    </section>

    <section class="card card--back" aria-label="Card back">
      <div class="pattern-field" role="img" aria-label="Faint repeating decorative pattern across the card back"></div>
      <p class="back-name">1876 Basins &amp; Spouts</p>
    </section>
  </main>
</body>
</html>
```